Business card design needed

I run a Beautician studio (for 7 years now)
I offer
- Velmo Body Sugaring
- Ruby Glaze
- Nails
- Facials
- Manicure
- Foot Treatment
It might not be necessary to list all those treatments?
Maybe the link to the Website is sufficient?
I leave that up to you ...
(more info on www.FernAndDewByLenka.com.au)
Velmo BodySugaring is our biggest success, It replaces waxing.
I would like to incorporate the logo into the Business Card.
We had many complaints regarding our old Business Cards as the Phone Number was to small.
On the backside, we would like a "your next Appointment" section.
Looking forward to you Design, cheers ... Lenka
Industry/Entity Type
Business
Contact Information for Business Card
Fern by Dew by Lenka
14 Korrin Sqr 3942 Berwick
www.FernAndDewByLenka.com.au
03 9481 2267

```html
<!DOCTYPE html>
<html lang="en">
<head>
<meta charset="utf-8">
<title>Fern &amp; Dew by Lenka — Business Cards</title>
<link rel="stylesheet" href="https://fonts.googleapis.com/css2?family=Open+Sans:ital,wght@0,400;0,600;1,700&family=Tinos&display=swap">
<style>
  :root {
    --stage: #ece9e4;
    --card: #ffffff;
    --band-dark: #58595b;
    --band-light: #bcbdbf;
    --ink: #231f20;
    --ink-soft: #3a3a3a;
    --rule: #9a9a9a;
    --title-light: #e8e8e8;
    --brand-sun: #f2a23a;
    --brand-faint: #efe8de;
  }
  * { box-sizing: border-box; margin: 0; padding: 0; }
  html, body { width: 1200px; height: 788px; overflow: hidden; }
  body {
    background: var(--stage);
    font-family: "Open Sans", Arial, sans-serif;
    color: var(--ink);
    position: relative;
  }
  .card {
    position: absolute;
    background: var(--card);
    border-radius: 22px;
    overflow: hidden;
    box-shadow: 0 3px 10px rgba(0,0,0,.25);
  }
  .card > * { position: absolute; }
  h1, h2 { font-weight: 400; }

  /* Front */
  .card-front { left: 337px; top: 73px; width: 526px; height: 302px; }
  .front-wave { left: 0; top: 0; width: 526px; height: 110px; }
  .front-title {
    right: 18px; top: 24px;
    font-size: 24px; letter-spacing: .5px;
    color: var(--title-light);
  }
  .brand-mark { display: flex; align-items: center; gap: 10px; }
  .brand-mark .dot {
    width: 34px; height: 34px; border-radius: 50%;
    background: var(--brand-sun); flex: none;
  }
  .brand-mark .name {
    font-size: 19px; font-weight: 600; color: var(--ink); letter-spacing: .5px;
  }
  .card-front .brand-mark { left: 24px; top: 190px; }
  .front-contact {
    right: 18px; top: 200px; font-style: normal;
    text-align: right; font-size: 16px; line-height: 26.5px; color: var(--ink);
  }
  .front-contact b { font-weight: 700; font-style: italic; }

  /* Back 1 */
  .card-back-one { left: 53px; top: 443px; width: 527px; height: 300px; }
  .back-faint-name {
    left: 0; right: 0; top: 182px; text-align: center;
    font-size: 46px; font-weight: 400; color: var(--brand-faint);
  }
  .back-one-title {
    left: 0; right: 0; top: 12px; text-align: center;
    font-size: 24px; letter-spacing: .8px; color: var(--ink-soft);
  }
  .back-one-rule { left: 0; right: 0; top: 51px; height: 1px; background: var(--rule); }
  .section-head { font-size: 17px; font-weight: 700; font-style: italic; }
  .offer-head { left: 30px; top: 70px; }
  .offer-list {
    left: 30px; top: 98px; list-style: none;
    font-family: "Tinos", "Times New Roman", serif; font-size: 15px; line-height: 20px;
    color: var(--ink-soft);
  }
  .offer-list li::before { content: "\25AA"; margin-right: 7px; font-size: 12px; }
  .column-divider { left: 207px; top: 76px; width: 2px; height: 144px; background: var(--rule); }
  .appt-head { left: 245px; top: 70px; }
  .appt-fields { left: 245px; top: 92px; font-size: 16px; color: var(--ink-soft); }
  .appt-fields p { display: flex; align-items: flex-end; height: 40px; }
  .blank { display: inline-block; border-bottom: 1px solid var(--ink-soft); height: 18px; }
  .back-one-hours-head { left: 0; right: 0; top: 238px; text-align: center; font-size: 14px; font-weight: 700; font-style: italic; }
  .back-one-hours { left: 62px; top: 262px; font-size: 13px; word-spacing: 1px; }
  .back-one-hours span + span { margin-left: 44px; }

  /* Back 2 */
  .card-back-two { left: 621px; top: 443px; width: 525px; height: 300px; }
  .hours-head { left: 33px; top: 28px; font-size: 21px; font-weight: 700; font-style: italic; letter-spacing: .6px; color: var(--ink-soft); }
  .hours-list { left: 30px; top: 60px; font-size: 18px; line-height: 24px; }
  .card-back-two .brand-mark { left: 382px; top: 40px; gap: 10px; }
  .card-back-two .brand-mark .dot { width: 36px; height: 36px; }
  .card-back-two .brand-mark .name { font-size: 19px; }
  .back-two-rule { left: 30px; width: 466px; top: 117px; height: 1px; background: var(--rule); }
  .next-appt { left: 46px; top: 143px; font-size: 18px; display: flex; align-items: flex-end; gap: 4px; }
  .date-line { left: 35px; top: 193px; font-size: 18px; display: flex; align-items: flex-end; gap: 6px; }
  .day-boxes { left: 60px; top: 248px; display: flex; gap: 14px; font-size: 17px; list-style: none; }
  .day-boxes li { display: flex; align-items: center; gap: 8px; }
  .day-boxes li::before {
    content: ""; width: 22px; height: 22px; border: 1.5px solid var(--ink);
  }
</style>
</head>
<body>

<section class="card card-front" aria-label="Card front">
  <svg class="front-wave" viewBox="0 0 526 110" aria-hidden="true">
    <path d="M0 0H526V104C440 98 330 110 220 80C140 58 60 48 0 62Z" fill="var(--band-light)"/>
    <path d="M0 0H526V90C440 84 330 96 220 66C140 44 60 34 0 46Z" fill="var(--band-dark)"/>
  </svg>
  <h1 class="front-title">FERN&amp;DEW BY LENKA</h1>
  <div class="brand-mark"><span class="dot"></span><span class="name">Velmo Body Sugaring</span></div>
  <address class="front-contact">
    <div><b>ph</b> 03 9481 2267</div>
    <div><b>a</b> 14 Korrin Sqr, 3942 Berwick</div>
    <div><b>w</b> www.FernAndDewByLenka.com.au</div>
  </address>
</section>

<section class="card card-back-one" aria-label="Card back, version one">
  <div class="back-faint-name" aria-hidden="true">Velmo</div>
  <h2 class="back-one-title">FERN&amp;DEW BY LENKA</h2>
  <div class="back-one-rule"></div>
  <h3 class="section-head offer-head">I offer</h3>
  <ul class="offer-list">
    <li>Velmo Body Sugaring</li>
    <li>Ruby Glaze</li>
    <li>Nails</li>
    <li>Facials</li>
    <li>Manicure</li>
    <li>Foot Treatment</li>
  </ul>
  <div class="column-divider"></div>
  <h3 class="section-head appt-head">An Appointment</h3>
  <div class="appt-fields">
    <p>Name<span class="blank" style="width:217px"></span></p>
    <p>Date<span class="blank" style="width:226px"></span></p>
    <p>time<span class="blank" style="width:160px"></span>&nbsp;am / pm</p>
  </div>
  <h3 class="back-one-hours-head">Hours of Operation</h3>
  <p class="back-one-hours"><span>Mon. to Fri. 7.30am - 7.00pm</span><span>Sat. 7.30am - 12.00pm</span></p>
</section>

<section class="card card-back-two" aria-label="Card back, version two">
  <h2 class="hours-head">Hours of Operation</h2>
  <div class="hours-list">
    <p>Monday to Friday - &nbsp;7.30am - 7.00pm</p>
    <p>Saturday - 7.30am - 12.00pm</p>
  </div>
  <div class="brand-mark"><span class="dot"></span><span class="name">Velmo</span></div>
  <div class="back-two-rule"></div>
  <p class="next-appt"><span class="blank" style="width:260px"></span>has an appointment</p>
  <p class="date-line">Date :<span class="blank" style="width:38px"></span>/<span class="blank" style="width:40px"></span>/<span class="blank" style="width:50px"></span>@<span class="blank" style="width:38px"></span>:<span class="blank" style="width:50px"></span>am / pm</p>
  <ul class="day-boxes">
    <li>Mon.</li><li>Tue.</li><li>Wed.</li><li>Thu.</li><li>Fri.</li>
  </ul>
</section>

</body>
</html>
```